Home Security Company Business Card

Looking for a eye catching business card that is non traditional and stands out but yet still looks professional. It should include all the pertinent information such as name, title, address, telephone, e-mail, website address should definitely stand out and then finally the logo.

Target Market(s)

Residential and Commercial accounts mostly upscale accounts

Industry/Entity Type

Security

Contact Information for Business Card

Name
Title
Address
Office #
Cell #
E-mail
Website

Font styles to use
Serif
Sans Serif

Requirements
Must have
• Logo, two sided color configuration
Nice to have
• You decide
Should not have
• There really aren't any.

```html
<!DOCTYPE html>
<html lang="en">
<head>
<meta charset="utf-8">
<title>Ironhold Protection Group – Business Card</title>
<link rel="stylesheet" href="https://fonts.googleapis.com/css2?family=Source+Sans+3:wght@400;600&display=swap">
<style>
  :root {
    --page-bg: #3b3b3b;
    --card-red: #731007;
    --card-white: #f7f7f7;
    --gold: #e0a73c;
    --gold-light: #f6d98a;
    --gold-deep: #b9781c;
    --text-light: #f4ece2;
    --brand-red: #7a140c;
  }
  * { margin: 0; padding: 0; box-sizing: border-box; }
  html, body { width: 1200px; height: 750px; overflow: hidden; }
  body {
    background: var(--page-bg);
    font-family: "Source Sans 3", "Segoe UI", sans-serif;
    position: relative;
  }
  .card {
    position: absolute;
    top: 228px;
    width: 461px;
    height: 262px;
    overflow: hidden;
  }
  .card--front { left: 144px; background: var(--card-red); }
  .card--back { left: 612px; background: var(--card-white); }

  .emblem-band {
    position: absolute;
    top: 0;
    height: 100%;
  }
  .card--front .emblem-band {
    right: 0;
    width: 86px;
    background: linear-gradient(90deg, rgba(224,167,60,0) 0%, var(--gold-deep) 30%, var(--gold-light) 80%, var(--gold) 100%);
  }
  .card--back .emblem-band {
    left: 0;
    width: 86px;
    background: linear-gradient(90deg, var(--brand-red) 0%, #a2321f 50%, rgba(247,247,247,0) 100%);
  }

  .contact {
    position: absolute;
    left: 46px;
    top: 52px;
    color: var(--text-light);
  }
  .contact__name {
    font-size: 17px;
    font-weight: 600;
    color: var(--gold);
    line-height: 1.1;
  }
  .contact__title {
    font-size: 13px;
    line-height: 1.35;
  }
  .contact__address {
    margin-top: 14px;
    font-size: 11.5px;
    line-height: 1.25;
  }
  .contact__list {
    list-style: none;
    margin-top: 8px;
    font-size: 11.5px;
  }
  .contact__list li {
    display: flex;
    align-items: center;
    height: 17.6px;
  }
  .contact__list svg {
    width: 11px;
    height: 11px;
    margin-right: 6px;
    fill: var(--gold);
    flex: none;
  }

  .brand {
    position: absolute;
    left: 180px;
    top: 116px;
    display: flex;
    align-items: center;
  }
  .brand__dot {
    width: 22px;
    height: 22px;
    border-radius: 50%;
    background: var(--brand-red);
    margin-right: 9px;
  }
  .brand__name {
    font-size: 17px;
    font-weight: 600;
    color: var(--brand-red);
    line-height: 1.05;
  }
</style>
</head>
<body>
  <section class="card card--front">
    <div class="emblem-band" role="img" aria-label="Large gold brand emblem decoration"></div>
    <div class="contact">
      <p class="contact__name">Marcus Reed</p>
      <p class="contact__title">CEO/Founder</p>
      <p class="contact__address">2140 Birchwood Drive<br>Juneau, Alaska 99801</p>
      <ul class="contact__list">
        <li>
          <svg viewBox="0 0 24 24" aria-hidden="true"><path d="M6.6 10.8a15.1 15.1 0 0 0 6.6 6.6l2.2-2.2c.3-.3.7-.4 1-.2 1.1.4 2.3.6 3.6.6.6 0 1 .4 1 1V20c0 .6-.4 1-1 1A17 17 0 0 1 3 4c0-.6.4-1 1-1h3.5c.6 0 1 .4 1 1 0 1.3.2 2.5.6 3.6.1.3 0 .7-.2 1z"/></svg>
          907 555 0142
        </li>
        <li>
          <svg viewBox="0 0 24 24" aria-hidden="true"><path d="M7 1h10a2 2 0 0 1 2 2v18a2 2 0 0 1-2 2H7a2 2 0 0 1-2-2V3a2 2 0 0 1 2-2zm0 3v15h10V4z"/></svg>
          907 555 0178
        </li>
        <li>
          <svg viewBox="0 0 24 24" aria-hidden="true"><path d="M2 5h20v14H2zm2 2v.5l8 5 8-5V7l-8 5z"/></svg>
          marcus@ironholdpro.com
        </li>
        <li>
          <svg viewBox="0 0 24 24" aria-hidden="true"><path d="M12 2a10 10 0 1 0 0 20 10 10 0 0 0 0-20zm-1 17.9A8 8 0 0 1 4.1 10L9 15v1a2 2 0 0 0 2 2zm6.9-2.5A2 2 0 0 0 16 16h-1v-3a1 1 0 0 0-1-1H8v-2h2a1 1 0 0 0 1-1V7h2a2 2 0 0 0 2-2v-.4a8 8 0 0 1 2.9 12.8z"/></svg>
          www.ironholdpro.com
        </li>
      </ul>
    </div>
  </section>

  <section class="card card--back">
    <div class="emblem-band" role="img" aria-label="Large red brand emblem decoration"></div>
    <div class="brand">
      <span class="brand__dot"></span>
      <p class="brand__name">Ironhold<br>Protection Group</p>
    </div>
  </section>
</body>
</html>
```